Harbourview Bat Club

I am looking to develop a sponsorship proposal using some of the imagery and colours 'black and gold' into a classy, professional laid out document to present to potential sponsors.
The content for the proposal/presentation is detailed in the "HBC Sponsor Deck". The HBC logo is featured in the black & gold presentations.

```html
<!DOCTYPE html>
<html lang="en">
<head>
<meta charset="utf-8">
<title>Harbourview Bat Club — Partnership Proposal</title>
<link rel="stylesheet" href="https://fonts.googleapis.com/css2?family=Libre+Caslon+Text:wght@400;700&family=Arimo:ital,wght@0,400;0,700;1,400&display=swap">
<style>
:root{
  --canvas:#c8c8c8;
  --black:#0f0e0d;
  --cream:#f5f0e6;
  --gold:#b8974f;
  --gold-light:#d4b46a;
  --ink:#1d1b18;
  --ink-soft:#3b3833;
  --white:#ffffff;
  --rule-dark:#3a3630;
  --rule-light:#d9d0bd;
  --serif:"Libre Caslon Text", Georgia, serif;
  --sans:"Arimo", Arial, sans-serif;
}
*{box-sizing:border-box;margin:0;padding:0}
html,body{width:1200px;height:2368px;overflow:hidden}
body{background:var(--canvas);position:relative;font-family:var(--sans);-webkit-font-smoothing:antialiased}
.slide{position:absolute;width:562px;height:316px;overflow:hidden}
.slide--dark{background:var(--black);color:var(--white)}
.slide--light{background:var(--cream);color:var(--ink)}
.slide > *{position:absolute}
.brand{top:20px;right:28px;display:flex;align-items:center;gap:4px;font-family:var(--serif);font-size:5.6px;letter-spacing:.04em;color:var(--gold);white-space:nowrap}
.brand::before{content:"";width:6px;height:6px;border-radius:50%;background:var(--gold)}
.foot{left:28px;top:300px;font-size:4.6px;font-weight:700;letter-spacing:.05em;text-transform:uppercase}
.slide--dark .foot{color:#bdb6a8}
.slide--light .foot{color:var(--ink-soft)}
.folio{right:28px;top:300px;font-size:4.8px;color:var(--gold)}
.title{font-family:var(--serif);font-weight:400;font-size:21px;line-height:1.12}
.body{font-size:6.9px;line-height:1.42}
.strong{font-weight:700}
.caps{text-transform:uppercase;font-weight:700;letter-spacing:.02em}
.ital{font-style:italic}
.gold{color:var(--gold)}
.list{list-style:none}
.list li{position:relative;padding-left:12px;font-size:6.9px}
.list li::before{content:"";position:absolute;left:2px;top:50%;width:2.4px;height:2.4px;margin-top:-1.2px;border-radius:50%;background:currentColor}
.photo{border-radius:6px}
.photo--framed{border:1px solid var(--gold)}
.photo--full{border-radius:0}
.row-list{font-size:6.9px;line-height:1}
.row-list .sep{margin:0 5px}
</style>
</head>
<body>

<section class="slide slide--dark" style="left:317px;top:22px">
  <div class="brand" style="left:28px;right:auto;top:38px">Harbourview Bat Club</div>
  <div class="caps gold" style="left:28px;top:64px;font-size:5px">2026 Sponsorship Proposal</div>
  <div style="left:28px;top:80px;width:40px;height:1px;background:var(--gold)"></div>
  <h1 class="title" style="left:0;width:276px;top:98px;text-align:center;font-size:28px;line-height:1.2;letter-spacing:.02em">PARTNERSHIP<br>PROPOSAL</h1>
  <div class="strong" style="left:0;width:276px;top:198px;text-align:center;font-size:9.5px;line-height:1.45;color:var(--gold-light)">Corporate Partnership &amp; Hospitality<br>Opportunities</div>
  <div class="caps" style="left:28px;top:281px;font-size:5px;color:#d8d2c4">More than cricket.</div>
  <div class="photo photo--full" role="img" aria-label="Cricket ground grandstand and light tower at sunset" style="left:276px;top:0;width:286px;height:316px;background:linear-gradient(180deg,#5d5b86 0%,#a77c8e 30%,#e2a46e 55%,#6c7a5a 72%,#2f6a3a 100%)"></div>
</section>

<section class="slide slide--dark" style="left:22px;top:355px">
  <div class="brand">Harbourview Bat Club</div>
  <h2 class="title" style="left:28px;top:36px;font-size:24px">More than cricket.</h2>
  <div class="body strong" style="left:28px;top:107px;font-size:8px">Invest in the game. Reward your people.</div>
  <div class="caps" style="left:28px;top:142px;font-size:7.8px;line-height:2.2">01&nbsp;&nbsp;Premium hospitality<br>02&nbsp;&nbsp;Exclusive experiences<br>03&nbsp;&nbsp;Community impact</div>
  <div class="photo photo--framed" role="img" aria-label="Floodlit cricket stadium full of spectators at night" style="left:265px;top:45px;width:270px;height:153px;background:radial-gradient(ellipse at 50% 65%,#4f8a3a 0%,#2f5e2a 35%,#1b2a30 60%,#0b1426 100%)"></div>
  <div class="photo photo--framed" role="img" aria-label="Suburban cricket oval with striped grass on a sunny day" style="left:296px;top:202px;width:207px;height:91px;background:linear-gradient(180deg,#7fb3e0 0%,#b9d7ee 35%,#4d7a3a 50%,#6fa24a 100%)"></div>
  <div class="foot">Harbourview Bat Club / Partnership Proposal</div>
  <div class="folio">02</div>
</section>

<section class="slide slide--light" style="left:608px;top:352px">
  <div class="brand">Harbourview Bat Club</div>
  <h2 class="title" style="left:28px;top:27px;width:280px">A legacy built to reinvest in the game</h2>
  <p class="body" style="left:28px;top:84px;width:255px">One of Australia’s oldest and most respected cricket clubs, Harbourview Bat Club is dedicated to growing cricket across Sydney and New South Wales.</p>
  <div class="body strong" style="left:28px;top:131px">Every sponsorship dollar is reinvested in:</div>
  <div class="body" style="left:28px;top:147px;line-height:2.35">Men’s and women’s Premier Cricket<br>Junior development programs and youth academies<br>Community coaching<br>Female participation and multicultural cricket<br>Facilities at Greyfield Oval</div>
  <p class="body ital" style="left:28px;top:240px;width:265px;line-height:1.4">Your investment creates opportunities for hundreds of young cricketers while connecting your business with one of Australia’s most iconic sporting institutions.</p>
  <div class="photo photo--framed" role="img" aria-label="Club team celebrating a premiership with trophy and banner" style="left:320px;top:62px;width:215px;height:144px;background:linear-gradient(180deg,#3b5e2e 0%,#5b7a3b 35%,#7b6a3a 55%,#2c4422 100%)"></div>
  <div style="left:320px;top:220px;width:215px;height:1px;background:var(--rule-light)"></div>
  <div style="left:330px;top:224px;font-family:var(--serif);font-size:35px;color:var(--gold);line-height:1">1897</div>
  <div class="caps" style="left:453px;top:234px;font-size:5.2px;line-height:1.5;color:var(--ink-soft)">Founded<br>Not-for-profit</div>
  <div class="foot">Harbourview Bat Club / Partnership Proposal</div>
  <div class="folio">03</div>
</section>

<section class="slide slide--dark" style="left:22px;top:687px">
  <div class="brand">Harbourview Bat Club</div>
  <h2 class="title" style="left:29px;top:23px;width:320px">Three advantages no ordinary sponsorship can match</h2>
  <div class="body" style="left:29px;top:71px">Three reasons make Harbourview Bat Club unique.</div>

  <div class="photo photo--framed" role="img" aria-label="Historic members’ pavilion with green roof" style="left:29px;top:94px;width:145px;height:76px;background:linear-gradient(180deg,#a9c7e0 0%,#8fae7e 35%,#3f6b3a 60%,#5c8a3e 100%)"></div>
  <div class="caps" style="left:29px;top:184px;font-size:6.4px">01&nbsp;&nbsp;Exclusive access</div>
  <div style="left:29px;top:200px;width:22px;height:1px;background:var(--gold)"></div>
  <p class="body" style="left:29px;top:209px;width:140px;font-size:6.4px;line-height:1.45;color:#d9d3c6">Our relationship with the Kestrel Park Ground and Lanterne Arena enables experiences that very few sporting organisations can provide.</p>

  <div class="photo photo--framed" role="img" aria-label="Women’s team holding a premiership banner" style="left:198px;top:94px;width:145px;height:76px;background:linear-gradient(180deg,#5a7a3a 0%,#2b3140 45%,#2a4aa0 70%,#3a5a2c 100%)"></div>
  <div class="caps" style="left:198px;top:184px;font-size:6.4px">02&nbsp;&nbsp;Women’s cricket leadership</div>
  <div style="left:198px;top:200px;width:22px;height:1px;background:var(--gold)"></div>
  <p class="body" style="left:198px;top:209px;width:140px;font-size:6.4px;line-height:1.45;color:#d9d3c6">Few clubs have produced more Australian and NSW women’s cricketers—including Mira Tennant, Josie Okafor, Priya Dunmore and Greta Lindqvist.</p>

  <div class="photo photo--framed" role="img" aria-label="Girls cricket academy session on a grass field" style="left:366px;top:94px;width:145px;height:76px;background:linear-gradient(180deg,#6a8f4a 0%,#4d7a36 45%,#3b2f3a 70%,#5c8a3e 100%)"></div>
  <div class="caps" style="left:366px;top:184px;font-size:6.4px">03&nbsp;&nbsp;Genuine community impact</div>
  <div style="left:366px;top:200px;width:22px;height:1px;background:var(--gold)"></div>
  <p class="body" style="left:366px;top:209px;width:145px;font-size:6.4px;line-height:1.45;color:#d9d3c6">Every partnership supports local cricket, junior development and the next generation of players across Sydney.</p>

  <div class="foot">Harbourview Bat Club / Partnership Proposal</div>
  <div class="folio">04</div>
</section>

<section class="slide slide--dark" style="left:608px;top:686px">
  <div class="photo photo--full" role="img" aria-label="Long dining table set for a silver-service lunch" style="left:0;top:0;width:264px;height:156px;background:linear-gradient(180deg,#6b5a22 0%,#c9b46a 40%,#e7dcae 70%,#b59a52 100%)"></div>
  <div class="photo photo--full" role="img" aria-label="Historic players’ dressing room with timber bar" style="left:0;top:156px;width:264px;height:160px;background:linear-gradient(180deg,#c7b262 0%,#8f7430 45%,#4a3418 75%,#2a1d10 100%)"></div>
  <div class="brand">Harbourview Bat Club</div>
  <h2 class="title" style="left:293px;top:40px;width:180px;font-size:17px">A signature experience beyond traditional hospitality</h2>
  <div style="left:465px;top:35px;width:58px;height:58px;border-radius:50%;background:var(--gold);color:var(--black);font-family:var(--serif);font-weight:700;text-align:center;padding-top:18px;font-size:9px;line-height:1.2">12<br>GUESTS</div>
  <div class="caps" style="left:293px;top:109px;width:240px;font-size:6.6px;line-height:1.4">Silver service lunch in the players’ dressing room</div>
  <p class="body" style="left:293px;top:139px;width:240px;font-size:6.6px">Host twelve of your most valued clients inside one of Australia’s most famous sporting venues.</p>
  <ul class="list" style="left:293px;top:168px">
    <li style="font-size:6.6px;line-height:16px">Private silver-service luncheon</li>
    <li style="font-size:6.6px;line-height:16px">Exclusive access to the players’ dressing room</li>
    <li style="font-size:6.6px;line-height:16px">Cricket guest speaker and behind-the-scenes stories</li>
    <li style="font-size:6.6px;line-height:16px">Premium wines and professional photographs</li>
  </ul>
  <div class="body strong" style="left:293px;top:238px;font-size:6.6px">Not available through traditional corporate hospitality.</div>
  <div class="foot">Harbourview Bat Club / Partnership Proposal</div>
  <div class="folio">05</div>
</section>

<section class="slide slide--light" style="left:22px;top:1020px">
  <div class="brand">Harbourview Bat Club</div>
  <h2 class="title" style="left:30px;top:28px;width:240px">Premium access across the sporting calendar</h2>
  <div class="body" style="left:30px;top:89px">Reward staff or entertain clients throughout the year.</div>
  <div class="caps" style="left:30px;top:104px;font-size:6.8px">Choose from</div>
  <ul class="list" style="left:30px;top:118px">
    <li style="line-height:15.5px">Australian International Cricket</li>
    <li style="line-height:15.5px">Ironbark Comets T20</li>
    <li style="line-height:15.5px">Marlowe Falcons Football</li>
    <li style="line-height:15.5px">Major rugby league fixture</li>
  </ul>
  <div class="caps" style="left:30px;top:183px;font-size:6.8px">Includes</div>
  <div class="body" style="left:30px;top:198px;line-height:2.3">Premium corporate suite, catering and beverages<br>Reserved seating and a dedicated host</div>
  <p class="body ital" style="left:30px;top:240px;width:240px;font-size:6.6px;line-height:1.4">Multiple events can be bundled into annual partnership packages across premium KPG hospitality formats.</p>
  <div class="photo photo--framed" role="img" aria-label="View over the cricket ground from a corporate suite" style="left:288px;top:52px;width:248px;height:125px;background:linear-gradient(180deg,#9fb3c3 0%,#6d7b6a 30%,#4f7f3e 55%,#2d2a26 100%)"></div>
  <div class="caps" style="left:288px;top:190px;width:76px;height:79px;border-radius:6px;background:var(--gold);color:var(--black);font-size:6.6px;text-align:center;padding-top:26px;line-height:1.35">Annual<br>packages<br>available</div>
  <div class="photo photo--framed" role="img" aria-label="Grandstands with the city skyline beyond" style="left:374px;top:190px;width:162px;height:79px;background:linear-gradient(180deg,#c2d4e2 0%,#9aa9a8 35%,#4d7a3a 60%,#6c9a4a 100%)"></div>
  <div class="foot">Harbourview Bat Club / Partnership Proposal</div>
  <div class="folio">06</div>
</section>

<section class="slide slide--dark" style="left:608px;top:1021px">
  <div class="photo photo--full" role="img" aria-label="Bowler in delivery stride at a net session with players watching" style="left:0;top:0;width:285px;height:316px;background:linear-gradient(180deg,#9aa58a 0%,#6f8560 30%,#3f5a36 60%,#1f2a1c 100%)"></div>
  <div class="photo photo--framed" role="img" aria-label="Batter playing a drive on the ground" style="left:169px;top:191px;width:113px;height:81px;background:linear-gradient(180deg,#5f8a42 0%,#4c7a34 60%,#3a6a2a 100%)"></div>
  <div class="brand">Harbourview Bat Club</div>
  <h2 class="title" style="left:313px;top:38px;width:230px">Play where Australia’s greats play</h2>
  <div class="caps" style="left:313px;top:104px;font-size:6.6px">A once-in-a-lifetime experience</div>
  <div class="body" style="left:313px;top:120px;font-size:6.6px">Twenty corporate guests—plus one child per guest—enjoy:</div>
  <ul class="list" style="left:313px;top:148px">
    <li style="font-size:6.6px;line-height:15.7px">Exclusive KPG net session</li>
    <li style="font-size:6.6px;line-height:15.7px">Australian cricketer host and coaching clinic</li>
    <li style="font-size:6.6px;line-height:15.7px">Family participation</li>
    <li style="font-size:6.6px;line-height:15.7px">BBQ overlooking the ground</li>
    <li style="font-size:6.6px;line-height:15.7px">Professional photographs</li>
  </ul>
  <div class="body strong" style="left:313px;top:241px;width:215px;font-size:6.6px;line-height:1.35">A memory your clients and their families will never forget.</div>
  <div class="caps" style="left:313px;top:271px;font-size:6.6px">20 corporate guests</div>
  <div class="foot">Harbourview Bat Club / Partnership Proposal</div>
  <div class="folio">07</div>
</section>

<section class="slide slide--light" style="left:22px;top:1357px">
  <div class="brand">Harbourview Bat Club</div>
  <h2 class="title" style="left:28px;top:26px;width:260px">Your own cricket day at Greyfield Oval</h2>
  <div class="body strong" style="left:28px;top:88px;font-size:7.3px">Bring your staff together or reward your best customers.</div>
  <div class="row-list" style="left:28px;top:105px"><span class="strong">Exclusive ground hire</span><span class="sep">•</span>Friendly cricket competition<span class="sep">•</span>BBQ<span class="sep">•</span>Music</div>
  <div class="row-list" style="left:28px;top:121px"><span class="strong">Team-building activities</span><span class="sep">•</span>Presentation ceremony<span class="sep">•</span>Optional former Australian player appearances</div>
  <div class="photo photo--framed" role="img" aria-label="Suburban oval surrounded by trees with a roller on the pitch" style="left:28px;top:155px;width:506px;height:129px;background:linear-gradient(180deg,#7fa9d8 0%,#c2d9ee 30%,#4f6f3a 45%,#6a9a44 70%,#89b25a 100%)"></div>
  <div class="caps" style="left:40px;top:269px;font-size:7px;color:var(--white)">Greyfield Oval</div>
  <div class="foot">Harbourview Bat Club / Partnership Proposal</div>
  <div class="folio">08</div>
</section>

<section class="slide slide--dark" style="left:608px;top:1356px">
  <div class="photo photo--full" role="img" aria-label="Women’s team celebrating with medals, trophy and state banner" style="left:273px;top:0;width:289px;height:316px;background:linear-gradient(180deg,#3a3f4a 0%,#6a5a3a 35%,#2c4a9a 65%,#1f2a3a 100%)"></div>
  <div class="photo photo--framed" role="img" aria-label="Players seated together in a dressing room" style="left:415px;top:184px;width:104px;height:98px;background:linear-gradient(180deg,#c9b47a 0%,#8a6a3a 50%,#3a2a1c 100%)"></div>
  <div class="brand">Harbourview Bat Club</div>
  <h2 class="title" style="left:28px;top:33px;width:220px">Back the home of women’s cricket</h2>
  <p class="body" style="left:28px;top:109px;width:225px;font-size:6.6px;line-height:2.2">HBC has helped develop some of Australia’s greatest female cricketers:</p>
  <ul class="list strong" style="left:28px;top:139px">
    <li style="font-size:6.6px;line-height:15.7px">Mira Tennant</li>
    <li style="font-size:6.6px;line-height:15.7px">Josie Okafor</li>
    <li style="font-size:6.6px;line-height:15.7px">Priya Dunmore</li>
    <li style="font-size:6.6px;line-height:15.7px">Greta Lindqvist</li>
    <li style="font-size:6.6px;line-height:15.7px">Tamsin Wrayburn</li>
  </ul>
  <p class="body strong" style="left:28px;top:229px;width:230px;font-size:6.6px;line-height:1.4">Today, we continue investing heavily in women’s cricket, pathways and youth development.</p>
  <p class="body" style="left:28px;top:259px;width:230px;font-size:6.6px;line-height:1.4">Supporting HBC means supporting the continued growth of women’s sport.</p>
  <div class="foot">Harbourview Bat Club / Partnership Proposal</div>
  <div class="folio">09</div>
</section>

<section class="slide slide--light" style="left:22px;top:1692px">
  <div class="brand">Harbourview Bat Club</div>
  <h2 class="title" style="left:28px;top:25px;width:320px">Community impact that reaches every week</h2>
  <div class="body strong" style="left:28px;top:76px">Each season Harbourview Bat Club supports:</div>
  <div class="row-list" style="left:28px;top:92px"><span class="strong">Premier Cricket</span><span class="sep">•</span>Women’s Cricket<span class="sep">•</span>Junior Academies<span class="sep">•</span>School programs</div>
  <div class="row-list" style="left:28px;top:108px"><span class="strong">Multicultural Cricket</span><span class="sep">•</span>Representative pathways<span class="sep">•</span>Community coaching<span class="sep">•</span>Volunteers</div>
  <div class="body ital" style="left:28px;top:122px;font-size:6.6px">Hundreds of players and families engage with our programs every week.</div>
  <div class="photo photo--framed" role="img" aria-label="Large group of junior players and families gathered on the field" style="left:28px;top:177px;width:175px;height:102px;background:linear-gradient(180deg,#8a9a7a 0%,#7a3a3a 40%,#e8e4dc 65%,#4a6a3a 100%)"></div>
  <div style="left:213px;top:177px;width:135px;height:102px;border-radius:6px;border:1px solid var(--gold);background:var(--black);overflow:hidden">
    <svg width="135" height="102" viewBox="0 0 135 102" style="position:absolute;left:0;top:0" aria-hidden="true">
      <path d="M0 78 C35 62 70 96 135 70 L135 102 L0 102 Z" fill="#f5f0e6"/>
      <path d="M0 74 C35 58 70 92 135 66" fill="none" stroke="#b8974f" stroke-width="1.2"/>
    </svg>
    <div class="caps" style="position:absolute;left:0;top:26px;width:135px;text-align:center;color:var(--white);font-size:8px;line-height:1.3">40+<br>Cultural<br>Backgrounds</div>
  </div>
  <div class="photo photo--framed" role="img" aria-label="Team group in front of ornate gates" style="left:358px;top:177px;width:176px;height:102px;background:linear-gradient(180deg,#2a2620 0%,#6a5a3a 40%,#1c2030 75%,#3a3a3a 100%)"></div>
  <div class="foot">Harbourview Bat Club / Partnership Proposal</div>
  <div class="folio">10</div>
</section>

<section class="slide slide--dark" style="left:608px;top:1692px">
  <div class="photo photo--full" role="img" aria-label="Batter in whites playing a shot in front of a white picket fence" style="left:370px;top:0;width:192px;height:316px;background:linear-gradient(180deg,#2a2a2a 0%,#5a4a3a 35%,#c9c2b0 55%,#6a8a4a 80%,#4a6a34 100%)"></div>
  <div style="left:372px;top:257px;width:150px;font-family:var(--serif);font-size:15px;line-height:1.1;color:var(--gold);opacity:.45;text-align:right">TAILORED<br>TO FIT</div>
  <div class="brand">Harbourview Bat Club</div>
  <h2 class="title" style="left:28px;top:26px;width:320px">One partnership, built around your goals</h2>
  <div class="strong" style="left:28px;top:83px;font-size:8.4px;color:var(--gold-light)">We tailor your partnership.</div>
  <div class="strong" style="left:28px;top:124px;font-size:6.6px">01&nbsp;&nbsp;Naming Rights</div>
  <div class="strong" style="left:185px;top:124px;font-size:6.6px">02&nbsp;&nbsp;Corporate Hospitality</div>
  <div style="left:28px;top:141px;width:140px;height:1px;background:var(--rule-dark)"></div>
  <div style="left:185px;top:141px;width:140px;height:1px;background:var(--rule-dark)"></div>
  <div class="strong" style="left:28px;top:158px;font-size:6.6px">03&nbsp;&nbsp;Women’s Cricket Partner</div>
  <div class="strong" style="left:185px;top:158px;font-size:6.6px">04&nbsp;&nbsp;Junior Academy Partner</div>
  <div style="left:28px;top:175px;width:140px;height:1px;background:var(--rule-dark)"></div>
  <div style="left:185px;top:175px;width:140px;height:1px;background:var(--rule-dark)"></div>
  <div class="strong" style="left:28px;top:192px;font-size:6.6px">05&nbsp;&nbsp;Community Partner</div>
  <div class="strong" style="left:185px;top:192px;font-size:6.6px">06&nbsp;&nbsp;Event Partner</div>
  <div style="left:28px;top:209px;width:140px;height:1px;background:var(--rule-dark)"></div>
  <div style="left:185px;top:209px;width:140px;height:1px;background:var(--rule-dark)"></div>
  <div class="strong" style="left:28px;top:226px;font-size:6.6px">07&nbsp;&nbsp;Staff Engagement Programs</div>
  <div class="strong" style="left:185px;top:226px;font-size:6.6px">08&nbsp;&nbsp;Client Entertainment Packages</div>
  <div class="foot">Harbourview Bat Club / Partnership Proposal</div>
  <div class="folio">11</div>
</section>

<section class="slide slide--light" style="left:22px;top:2026px">
  <div class="brand">Harbourview Bat Club</div>
  <h2 class="title" style="left:28px;top:25px;width:400px">Value for your business. Value for the game.</h2>
  <div class="caps" style="left:28px;top:97px;font-size:6.8px">For your business</div>
  <ul class="list" style="left:28px;top:127px">
    <li style="line-height:16.6px">Premium client entertainment</li>
    <li style="line-height:16.6px">Staff engagement</li>
    <li style="line-height:16.6px">Brand alignment</li>
    <li style="line-height:16.6px">Corporate networking</li>
    <li style="line-height:16.6px">Unique experiences</li>
  </ul>
  <div class="caps" style="left:309px;top:97px;font-size:6.8px">For the community</div>
  <ul class="list" style="left:309px;top:115px">
    <li style="line-height:11px">Better facilities</li>
    <li style="line-height:11px">Junior participation</li>
    <li style="line-height:11px">Women’s cricket</li>
    <li style="line-height:11px">Community programs</li>
    <li style="line-height:11px">Future Australian players</li>
  </ul>
  <div class="photo photo--framed" role="img" aria-label="Guests at a corporate dinner in a grand room" style="left:28px;top:227px;width:224px;height:53px;background:linear-gradient(180deg,#3a3a4a 0%,#8a6a4a 45%,#c9a87a 70%,#4a3a2a 100%)"></div>
  <div class="photo photo--framed" role="img" aria-label="Historic team portrait of players in whites" style="left:309px;top:227px;width:225px;height:53px;background:linear-gradient(180deg,#3a3028 0%,#d8d0c0 40%,#8a7a62 70%,#2a241c 100%)"></div>
  <div class="foot">Harbourview Bat Club / Partnership Proposal</div>
  <div class="folio">12</div>
</section>

<section class="slide slide--dark" style="left:608px;top:2026px">
  <div class="photo photo--full" role="img" aria-label="Cricket ground grandstand and light tower at dusk" style="left:284px;top:0;width:278px;height:316px;background:linear-gradient(180deg,#3a3848 0%,#7a6a7a 25%,#c9936a 50%,#5a6a4a 68%,#2f6a3a 100%)"></div>
  <h2 class="title" style="left:31px;top:52px;width:250px;font-size:22px">Let’s build something bigger than cricket</h2>
  <p class="body" style="left:31px;top:134px;width:225px;font-size:6.9px">When your business partners with Harbourview Bat Club, you become part of something much larger than cricket.</p>
  <p class="body" style="left:31px;top:172px;width:225px;font-size:6.9px">Build stronger communities. Develop future Australian representatives. Create unforgettable experiences for your staff and clients.</p>
  <div class="body strong" style="left:31px;top:214px">Together, we can grow the game.</div>
  <div class="caps" style="left:31px;top:255px;font-size:6.8px;color:var(--gold)">Grow the game.</div>
  <div class="brand" style="left:31px;right:auto;top:284px;font-size:6.2px">Harbourview Bat Club</div>
</section>

</body>
</html>
```